Velmora Systems Website

Website design for our company: Velmora Systems.
The website should look fresh and IT focused. Please have a look at http://www.velmorasystems.example.au/ for our current design. We want something fresh and new, professional looking, in WordPress so we can easily make changes.

It Company

```html
<!DOCTYPE html>
<html lang="en">
<head>
<meta charset="utf-8">
<title>Velmora Systems</title>
<link href="https://fonts.googleapis.com/css2?family=Roboto:wght@400;500&display=swap" rel="stylesheet">
<style>
:root{
  --green:#06b050;
  --blue:#0a6cc4;
  --blue-dark:#0759a8;
  --head:#1a73c1;
  --text:#444;
  --leaf:#4db81f;
  --black:#050505;
}
*{margin:0;padding:0;box-sizing:border-box}
html,body{width:1200px;height:1136px;overflow:hidden}
body{position:relative;background:#fff;font-family:"Roboto",Arial,sans-serif;color:var(--text)}
.abs{position:absolute}
.top-strip{left:0;top:0;width:1200px;height:8px;background:var(--green)}
.header{left:0;top:8px;width:1200px;height:108px;background:linear-gradient(#fafafa,#e4e4e4);border-bottom:3px solid var(--blue)}
.logo{left:200px;top:8px;width:170px;height:91px;background:var(--green);display:flex;align-items:center;justify-content:center;gap:8px}
.logo-dot{width:14px;height:14px;border-radius:50%;background:#fff}
.logo-name{color:#fff;font-weight:500;font-size:17px;line-height:1.1;text-align:left}
.search{left:814px;top:26px;width:186px;height:32px;background:#fff;border:1px solid #ccc;font-size:10.5px;color:#333;padding:9px 0 0 6px}
.search svg{position:absolute;right:10px;top:10px}
.nav{left:518px;top:71px;width:682px;height:45px;background:var(--blue);clip-path:polygon(42px 0,100% 0,100% 100%,0 100%);display:flex;align-items:center;padding-left:42px}
.nav a{color:#fff;text-decoration:none;font-size:10.5px;margin-left:20px;display:flex;align-items:center}
.nav a::before{content:"";width:7px;height:7px;border-radius:50%;background:var(--leaf);margin-right:4px}
.hero{left:0;top:116px;width:1200px;height:458px;background:linear-gradient(100deg,#6aa9c9 0%,#9fd0e6 30%,#cdeaf5 52%,#8fc2da 70%,#2f5f86 88%,#27405e 100%)}
.slide-tag{background:var(--blue);color:#fff;font-size:24px;display:flex;align-items:center;justify-content:center}
.tag-one{left:199px;top:261px;width:211px;height:72px}
.tag-two{left:258px;top:345px;width:356px;height:72px}
.arrow{top:292px}
.dots{left:571px;top:542px;display:flex;gap:7px}
.dots span{width:11px;height:11px;border-radius:50%;background:#fff;border:1px solid #888}
.dots span.on{background:var(--blue);border-color:#fff}
h2{font-weight:400;color:var(--head)}
.welcome-title{left:201px;top:602px;font-size:26px}
.welcome-copy{left:200px;top:640px;width:470px;font-size:10px;line-height:19.2px}
.welcome-photo{left:694px;top:598px;width:306px;height:179px;border:2px solid #ddd;background:linear-gradient(120deg,#f1f3f5 0%,#cfe3ef 45%,#5b8fb5 65%,#e8eef2 100%)}
.services-title{left:201px;top:814px;font-size:26px}
.services-intro{left:200px;top:857px;width:470px;font-size:11.5px;line-height:16px;color:#111}
.services-sub{left:200px;top:898px;font-size:11.5px;color:var(--green)}
.svc{font-size:10px;color:#444;display:flex;align-items:center}
.svc svg{margin-right:10px}
.remote-title{left:690px;top:819px;font-size:20px}
.remote-box{left:690px;top:858px;width:310px;height:171px;border:1px solid #ccc;background:#fff}
.remote-head{left:708px;top:873px;font-size:15px;color:#4aa81e}
.remote-note{left:708px;top:898px;font-size:9px;color:#aaa}
.remote-input{left:709px;top:923px;width:270px;height:39px;border:1px solid #999;border-radius:5px;background:linear-gradient(#fff,#e9e9e9)}
.remote-btn{left:878px;top:974px;width:101px;height:38px;background:var(--blue);color:#fff;font-size:11.5px;display:flex;align-items:center;justify-content:center}
.footer{left:0;top:1074px;width:1200px;height:62px;background:var(--black)}
.copyright{left:199px;top:1096px;font-size:10.5px;color:#fff}
.social{top:1091px;width:26px;height:26px}
</style>
</head>
<body>
<div class="abs top-strip"></div>
<header class="abs header"></header>
<div class="abs logo"><span class="logo-dot"></span><span class="logo-name">Velmora<br>Systems</span></div>
<div class="abs search">Search...
  <svg width="12" height="12" viewBox="0 0 12 12"><circle cx="5" cy="5" r="3.8" fill="none" stroke="#333" stroke-width="1.4"/><path d="M8 8l3 3" stroke="#333" stroke-width="1.4"/></svg>
</div>
<nav class="abs nav">
  <a href="#">Home</a><a href="#">Clients</a><a href="#">Services</a><a href="#">Testimonials</a><a href="#">Contact Us</a><a href="#">About Us</a>
</nav>

<section class="abs hero" role="img" aria-label="Hand touching a glowing digital interface with world map and data graphics"></section>
<div class="abs slide-tag tag-one">Velmora Systems</div>
<div class="abs slide-tag tag-two">Adelaide based company</div>
<svg class="abs arrow" style="left:62px" width="20" height="32" viewBox="0 0 20 32"><path d="M16 3L5 16l11 13" fill="none" stroke="#fff" stroke-width="5"/></svg>
<svg class="abs arrow" style="left:1124px" width="20" height="32" viewBox="0 0 20 32"><path d="M4 3l11 13L4 29" fill="none" stroke="#fff" stroke-width="5"/></svg>
<div class="abs dots"><span class="on"></span><span></span><span></span></div>

<h2 class="abs welcome-title">Welcome to Velmora Systems</h2>
<div class="abs welcome-copy">
  <p>Velmora Systems is an Adelaide based company with a single objective - to excel in the support and service of all computer and IT needs.</p>
  <p>We provide a high level of consulting services using the most experienced engineers at a reasonable and fair price. We believe in using a Business Value approach to every aspect of computer consulting to provide our clients with the most cost effective solutions.</p>
  <p>We strongly believe that we are in business with our clients. Each thing we do must be measured against our clients' business objectives. At the end of the day our client's success is our success.</p>
</div>
<div class="abs welcome-photo" role="img" aria-label="Person at a laptop with a glowing world map of images"></div>

<h2 class="abs services-title">Our Services</h2>
<p class="abs services-intro">Velmora Systems is an Adelaide based company with a single objective - to excel in the support and service of all computer and IT needs.</p>
<p class="abs services-sub">Velmora Systems Services :</p>

<div class="abs svc" style="left:203px;top:929px"><svg width="15" height="13" viewBox="0 0 15 13"><path d="M1 7l4 4 9-10" fill="none" stroke="#4db81f" stroke-width="2.4"/></svg>On-site Service</div>
<div class="abs svc" style="left:203px;top:953px"><svg width="15" height="13" viewBox="0 0 15 13"><path d="M1 7l4 4 9-10" fill="none" stroke="#4db81f" stroke-width="2.4"/></svg>Remote Desktop Support</div>
<div class="abs svc" style="left:203px;top:977px"><svg width="15" height="13" viewBox="0 0 15 13"><path d="M1 7l4 4 9-10" fill="none" stroke="#4db81f" stroke-width="2.4"/></svg>Medical IT Service</div>
<div class="abs svc" style="left:203px;top:1001px"><svg width="15" height="13" viewBox="0 0 15 13"><path d="M1 7l4 4 9-10" fill="none" stroke="#4db81f" stroke-width="2.4"/></svg>Pharmacy IT Service</div>
<div class="abs svc" style="left:380px;top:929px"><svg width="15" height="13" viewBox="0 0 15 13"><path d="M1 7l4 4 9-10" fill="none" stroke="#4db81f" stroke-width="2.4"/></svg>Website Design</div>
<div class="abs svc" style="left:380px;top:953px"><svg width="15" height="13" viewBox="0 0 15 13"><path d="M1 7l4 4 9-10" fill="none" stroke="#4db81f" stroke-width="2.4"/></svg>Disaster Recovery</div>
<div class="abs svc" style="left:380px;top:977px"><svg width="15" height="13" viewBox="0 0 15 13"><path d="M1 7l4 4 9-10" fill="none" stroke="#4db81f" stroke-width="2.4"/></svg>Hardware/ Software supply</div>
<div class="abs svc" style="left:380px;top:1001px"><svg width="15" height="13" viewBox="0 0 15 13"><path d="M1 7l4 4 9-10" fill="none" stroke="#4db81f" stroke-width="2.4"/></svg>Consumablesz</div>

<h2 class="abs remote-title">Remote Support</h2>
<div class="abs remote-box"></div>
<div class="abs remote-head">Enter your 6-digit code</div>
<div class="abs remote-note">Velmora Systems is an Adelaide Systems is an Adelaide</div>
<div class="abs remote-input"></div>
<div class="abs remote-btn">Connect Now</div>

<footer class="abs footer"></footer>
<div class="abs copyright">Copyright © 2013 Velmora Systems Pty Ltd. All Rights Reserved.</div>
<div class="abs social" style="left:851px;background:#3b5a9a" aria-label="Social link"></div>
<div class="abs social" style="left:893px;background:#3f6e9a" aria-label="Social link"></div>
<div class="abs social" style="left:934px;background:#2aa6dd" aria-label="Social link"></div>
<div class="abs social" style="left:973px;background:#d92626" aria-label="Social link"></div>
</body>
</html>
```